Falkrin homes and renovations business card design.

Would like some new card designs utilizing my new logo that look professional. I am open to different colors on the logo or utilize the same ones we have. I like the original concept but would like to see some fresh ideas and build on what we have already done.

Target Market(s)

Custom home building industry, Real estate sales, Renovation projects.

Industry/Entity Type

Home Builder

Contact Information for Business Card

Falkrin Homes and Renovations
2871 96th Avenue
Ashvale, Norland
T2R3W8
Home : 555- 718-4063 Cell: 555- 294-5170

My info is : Dax Falkrin, President and CEO
email: falkrinhomes@maildrop-example.net
Website: falkrinhomes-example.com
websit

Requirements
Must have
• Must Use my new logo design. I am open to different colors on the logo or utilize the same ones in the existing design. I can upload the original logo design if needed.

```html
<!DOCTYPE html>
<html lang="en">
<head>
<meta charset="utf-8">
<title>Falkrin Homes and Renovations – Business Cards</title>
<link href="https://fonts.googleapis.com/css2?family=Montserrat:wght@400;500;600;700&display=swap" rel="stylesheet">
<style>
  :root {
    --backdrop: #3a3a3a;
    --card-black: #060606;
    --card-white: #ffffff;
    --gold: #b5883a;
    --yellow: #f2b31c;
    --ink: #555555;
    --light: #f4f4f4;
  }
  * { box-sizing: border-box; margin: 0; padding: 0; }
  html, body { width: 1200px; height: 864px; overflow: hidden; }
  body {
    background: var(--backdrop);
    font-family: "Montserrat", sans-serif;
    position: relative;
  }
  .card {
    position: absolute;
    top: 278px;
    width: 540px;
    height: 309px;
    border-radius: 18px;
    overflow: hidden;
    box-shadow: 0 14px 30px rgba(0,0,0,.45);
  }
  .card--back { left: 40px; background: var(--card-black); }
  .card--front { left: 620px; background: var(--card-white); }

  .brand {
    position: absolute;
    left: 0; right: 0;
    display: flex;
    align-items: center;
    justify-content: center;
    gap: 12px;
  }
  .brand__mark { width: 14px; height: 14px; background: var(--gold); }
  .brand__name {
    font-weight: 700;
    font-size: 24px;
    letter-spacing: .5px;
    color: var(--gold);
  }
  .card--back .brand { top: 112px; }
  .card--front .brand { top: 42px; }

  .back__url {
    position: absolute;
    top: 206px; left: 0; right: 0;
    text-align: center;
    color: var(--light);
    font-size: 13px;
    letter-spacing: .4px;
  }

  .band {
    position: absolute;
    top: 120px; left: 0; right: 0;
    height: 64px;
    background: var(--gold);
    text-align: center;
    padding-top: 12px;
  }
  .band__name { color: var(--yellow); font-weight: 700; font-size: 19px; line-height: 22px; }
  .band__title { color: #fff; font-size: 13px; line-height: 18px; }

  .contacts {
    position: absolute;
    left: 28px; bottom: 26px;
    list-style: none;
    font-size: 13px;
    color: var(--ink);
    line-height: 22px;
  }
  .contacts li { display: flex; align-items: center; gap: 8px; }
  .contacts svg { width: 13px; height: 13px; fill: var(--yellow); flex: none; }

  .address {
    position: absolute;
    right: 26px; top: 198px;
    text-align: right;
    font-size: 12.5px;
    line-height: 19px;
    color: var(--ink);
    font-style: normal;
  }
  .address__web { color: var(--gold); }
</style>
</head>
<body>
  <section class="card card--back" aria-label="Card back">
    <div class="brand">
      <span class="brand__mark"></span>
      <span class="brand__name">Falkrin Homes and Renovations</span>
    </div>
    <p class="back__url">www.falkrinhomes-example.com</p>
  </section>

  <section class="card card--front" aria-label="Card front">
    <div class="brand">
      <span class="brand__mark"></span>
      <span class="brand__name">Falkrin Homes and Renovations</span>
    </div>

    <div class="band">
      <p class="band__name">Dax Falkrin</p>
      <p class="band__title">President and CEO</p>
    </div>

    <address class="address">
      2871 96th Avenue<br>
      Ashvale, Norland, T2R3W8<br>
      <span class="address__web">falkrinhomes-example.com</span>
    </address>

    <ul class="contacts">
      <li>
        <svg viewBox="0 0 16 16" aria-hidden="true"><path d="M3.6 1.2l2.3 2.6-1.3 1.8c.9 2 2.3 3.5 4.3 4.5l1.8-1.3 2.6 2.3-1.4 2.6C6.8 13.5 2.5 9.2 1 4.1z"/></svg>
        555- 718-4063
      </li>
      <li>
        <svg viewBox="0 0 16 16" aria-hidden="true"><path d="M4.5 0h7a1 1 0 0 1 1 1v14a1 1 0 0 1-1 1h-7a1 1 0 0 1-1-1V1a1 1 0 0 1 1-1zm.6 2v10.5h5.8V2zM8 13.3a.9.9 0 1 0 0 1.8.9.9 0 0 0 0-1.8z"/></svg>
        555- 294-5170
      </li>
      <li>
        <svg viewBox="0 0 16 16" aria-hidden="true"><path d="M0 3h16v10H0zm1.6 1.2L8 9l6.4-4.8z"/></svg>
        falkrinhomes@maildrop-example.net
      </li>
    </ul>
  </section>
</body>
</html>
```